Business card for my new company (Accounting firm)

I need a business card for my new business Brightwell Advisory and Ledger SA. Our services are accounting, tax, audit and financial management. Our customers are small companies, start-ups and new companies. The final design has to show financial security, trust and growth. Please find our logo attached to the business card. Text for the business card: Brightwell Advisory and Ledger SA Tomas Varenholt Director and Founder Certified Accountant Tel. 022 418 57 34 tv@clairevalconseil.ch www.clairevalconseil.ch Rue des Vergières 27 1201 Geneva
Target Market(s)
Our customers are small companies, start-ups and new companies.
Industry/Entity Type
Finance And Accounting
Contact Information for Business Card
Claireval Conseil et Comptes SA
Tomas Varenholt
Directeur et Fondateur
Expert-comptable diplômé
Tél. 022 418 57 34
tv@clairevalconseil.ch
www.clairevalconseil.ch
Rue des Vergières 27
1201 Genève

```html
<!DOCTYPE html>
<html lang="fr">
<head>
<meta charset="utf-8">
<title>Claireval Conseil et Comptes SA – Carte de visite</title>
<link rel="stylesheet" href="https://fonts.googleapis.com/css2?family=Montserrat:wght@300;500;600&family=Roboto:wght@400;700&display=swap">
<style>
  :root {
    --bg: #e9eaec;
    --blue-light: #2ca6d9;
    --blue-dark: #1c6c9c;
    --navy: #1d5d93;
    --ink: #3a3f45;
    --text: #2f3338;
    --paper: #f7f7f8;
    --white: #ffffff;
  }
  * { box-sizing: border-box; margin: 0; padding: 0; }
  html, body {
    width: 1200px; height: 726px; overflow: hidden;
    background: var(--bg);
  }
  .stage { position: relative; width: 1200px; height: 726px; }

  .card {
    position: absolute;
    width: 520px; height: 315px;
    border-radius: 4px;
    box-shadow: 0 10px 28px rgba(0,0,0,.14);
    overflow: hidden;
  }

  /* Front */
  .card--front {
    left: 60px; top: 110px;
    background: linear-gradient(160deg, var(--blue-light) 0%, var(--blue-dark) 100%);
    color: var(--white);
    display: flex; flex-direction: column; align-items: center; justify-content: center;
  }
  .front__name {
    font-family: "Montserrat", sans-serif;
    font-weight: 500;
    font-size: 50px;
    letter-spacing: 6px;
    line-height: 1;
  }
  .front__tagline {
    font-family: "Montserrat", sans-serif;
    font-weight: 300;
    font-size: 17px;
    letter-spacing: 4.2px;
    margin-top: 8px;
  }
  .front__web {
    position: absolute; bottom: 42px; left: 0; right: 0;
    text-align: center;
    font-family: "Roboto", sans-serif;
    font-weight: 700;
    font-size: 15px;
    letter-spacing: .3px;
  }

  /* Back */
  .card--back {
    left: 620px; top: 300px;
    background: var(--paper);
    color: var(--text);
    font-family: "Roboto", sans-serif;
  }
  .person { position: absolute; left: 36px; top: 70px; }
  .person__name { color: var(--navy); font-weight: 700; font-size: 20px; }
  .person__role { font-size: 12.5px; line-height: 1.35; margin-top: 4px; }

  .contact { position: absolute; left: 36px; bottom: 34px; font-size: 13px; line-height: 1.45; }
  .contact__address { margin-bottom: 6px; }
  .contact__line { display: flex; align-items: center; gap: 10px; }
  .contact__icon { width: 12px; height: 12px; fill: var(--navy); flex: none; }

  .brand {
    position: absolute; right: 30px; top: 126px;
    display: flex; align-items: center; gap: 12px;
    color: var(--ink);
    font-family: "Montserrat", sans-serif;
    font-weight: 600;
  }
  .brand__mark { width: 22px; height: 22px; background: var(--blue-light); }
  .brand__name { font-size: 30px; letter-spacing: 3px; line-height: 1; }
  .brand__tagline { font-size: 10px; letter-spacing: 2.6px; margin-top: 6px; }
</style>
</head>
<body>
<main class="stage">
  <section class="card card--front" aria-label="Recto">
    <div class="front__name">CLAIREVAL</div>
    <div class="front__tagline">CONSEIL ET COMPTES</div>
    <div class="front__web">www.clairevalconseil.ch</div>
  </section>

  <section class="card card--back" aria-label="Verso">
    <div class="person">
      <div class="person__name">Tomas Varenholt</div>
      <div class="person__role">Directeur et Fondateur<br>Expert-comptable diplômé</div>
    </div>

    <div class="contact">
      <div class="contact__address">Rue des Vergières 27<br>1201 Genève</div>
      <div class="contact__line">
        <svg class="contact__icon" viewBox="0 0 12 12" aria-hidden="true"><path d="M2.4 1h2l1 2.6-1.3 1a6 6 0 0 0 3.3 3.3l1-1.3L11 7.6v2c0 .8-.6 1.4-1.4 1.4A9.6 9.6 0 0 1 1 2.4C1 1.6 1.6 1 2.4 1z"/></svg>
        <span>022 418 57 34</span>
      </div>
      <div class="contact__line">
        <svg class="contact__icon" viewBox="0 0 12 12" aria-hidden="true"><path d="M0 2.5h12v7H0z M1 3.3 6 7l5-3.7" fill="var(--navy)" stroke="var(--paper)" stroke-width=".9"/></svg>
        <span>tv@clairevalconseil.ch</span>
      </div>
      <div class="contact__line">
        <svg class="contact__icon" viewBox="0 0 12 12" aria-hidden="true"><circle cx="6" cy="6" r="5.5"/><path d="M.5 6h11M6 .5c-2.4 3-2.4 8 0 11M6 .5c2.4 3 2.4 8 0 11" stroke="var(--paper)" stroke-width=".8" fill="none"/></svg>
        <span>www.clairevalconseil.ch</span>
      </div>
    </div>

    <div class="brand">
      <div class="brand__mark" aria-hidden="true"></div>
      <div>
        <div class="brand__name">CLAIREVAL</div>
        <div class="brand__tagline">CONSEIL ET COMPTES</div>
      </div>
    </div>
  </section>
</main>
</body>
</html>
```